Lucky Harbour Fun Casino Entertainment

Looking to update my business card and make it look more modern, stand out and eye catching.
We are are fun casino business in Australia (primarily Sydney). Blackjack and Roulette are our most popular games although we have pretty much every game available for hire that you would find in a real casino. The final design would need to be sleek and appeal to the more upmarket corporate sector.
We mainly cater for Corporate Events, Private Parties, Fundraising Events, Team Building, Poker Tournaments
I think I'd prefer the colour Black.

Target Market(s)

High-end Corporate

Industry/Entity Type

Events

Contact Information for Business Card

Rob Kendall
Director
1300 482 617
0433 728 591
info@luckyharbour.com.au
www.luckyharbour.com.au
Facebook & Instagram @luckyharbourevents (proper social icons preferred)

Colors
000000
0255a3

Requirements
Must have
• Front side:
• Logo
• Contact details
• 'Australia's #1 Fun Casino Specialists'
• Back:
• Logo
Nice to have
• Back:
• Corporate Events
• Private Parties
• Poker Tournaments
• Fundraising
• Props & Theming
• Photo Booth
• Horse Racing Events
• The Vegas Sign attached, maybe on the back of the card in the background...?

```html
<!DOCTYPE html>
<html lang="en">
<head>
<meta charset="utf-8">
<title>Lucky Harbour Fun Casino Entertainment – Business Card</title>
<link href="https://fonts.googleapis.com/css2?family=Lato:wght@400;700&display=swap" rel="stylesheet">
<style>
  :root {
    --stage: #2a2a2c;
    --card: #1d1e20;
    --orange: #f7a824;
    --yellow: #f2d428;
    --grey: #c4c4c4;
    --white: #f2f2f2;
    --line: #8a8a8a;
    --mark: #2e2f32;
  }
  * { margin: 0; padding: 0; box-sizing: border-box; }
  html, body { width: 1200px; height: 1108px; overflow: hidden; background: var(--stage); }
  body { font-family: "Lato", sans-serif; position: relative; }
  .card {
    position: absolute; top: 234px; width: 400px; height: 640px;
    background: var(--card); border-radius: 20px;
    box-shadow: 0 18px 40px rgba(0,0,0,.45);
    display: flex; flex-direction: column; align-items: center; text-align: center;
  }
  .card--front { left: 160px; }
  .card--back { left: 640px; }
  .brand { display: flex; flex-direction: column; align-items: center; margin-top: 86px; }
  .brand__disc { width: 110px; height: 110px; border-radius: 50%; background: var(--mark); }
  .brand__name {
    margin-top: 16px; font-size: 34px; font-weight: 700; color: var(--orange);
    text-transform: uppercase; letter-spacing: 1px;
  }
  .person__name { margin-top: 54px; font-size: 28px; font-weight: 400; color: var(--orange); text-transform: uppercase; }
  .person__role { font-size: 19px; color: var(--grey); margin-top: 2px; }
  .divider { display: flex; align-items: center; gap: 8px; width: 230px; margin-top: 12px; }
  .divider::before, .divider::after { content: ""; flex: 1; height: 1px; background: var(--line); }
  .divider svg { display: block; }
  .contacts { list-style: none; margin-top: 8px; font-size: 19px; line-height: 28px; color: var(--grey); }
  .handle { font-size: 19px; color: var(--grey); margin-top: 4px; }
  .divider--social { margin-top: 14px; }
  .tagline {
    margin-top: 44px; font-size: 26px; line-height: 32px; color: var(--yellow);
    text-transform: uppercase; font-weight: 400;
  }
  .services { list-style: none; margin-top: 40px; font-size: 20px; line-height: 29px; color: var(--white); }
</style>
</head>
<body>
  <section class="card card--front">
    <div class="brand">
      <div class="brand__disc"></div>
      <div class="brand__name">Lucky Harbour</div>
    </div>
    <h1 class="person__name">Rob Kendall</h1>
    <p class="person__role">Director</p>
    <div class="divider">
      <svg width="104" height="22" viewBox="0 0 104 22" aria-hidden="true">
        <g fill="#f7a824">
          <circle cx="11" cy="11" r="11"/><circle cx="38" cy="11" r="11"/>
          <circle cx="65" cy="11" r="11"/><circle cx="92" cy="11" r="11"/>
        </g>
        <g fill="none" stroke="#1d1e20" stroke-width="1.8">
          <path d="M6 9c0-2 2-3 5-3s5 1 5 3M8 10h6v5H8z"/>
          <rect x="34.5" y="5" width="7" height="12" rx="1"/>
          <rect x="59" y="7" width="12" height="8"/><path d="M59 7l6 5 6-5"/>
          <circle cx="92" cy="11" r="6"/><path d="M86 11h12M92 5c-3 3-3 9 0 12M92 5c3 3 3 9 0 12"/>
        </g>
      </svg>
    </div>
    <ul class="contacts">
      <li>1300 482 617</li>
      <li>0433 728 591</li>
      <li>info@luckyharbour.com.au</li>
      <li>www.luckyharbour.com.au</li>
    </ul>
    <div class="divider divider--social">
      <svg width="22" height="22" viewBox="0 0 22 22" aria-hidden="true"><circle cx="11" cy="11" r="11" fill="#0255a3"/></svg>
    </div>
    <p class="handle">@luckyharbourevents</p>
  </section>

  <section class="card card--back">
    <div class="brand">
      <div class="brand__disc"></div>
      <div class="brand__name">Lucky Harbour</div>
    </div>
    <h2 class="tagline">Australia's #1 Fun<br>Casino Specialists</h2>
    <ul class="services">
      <li>Corporate Events</li>
      <li>Private Parties</li>
      <li>Poker Tournaments</li>
      <li>Fundraising</li>
      <li>Props &amp; Theming</li>
      <li>Photo Booth</li>
      <li>Horse Racing Events</li>
    </ul>
  </section>
</body>
</html>
```